Award-winnning Estate Agent needs a premium version of their 'For Sale' board design

We need a premium option for our 'For Sale' board design. We have a standard board that is attached to this brief, but were are looking to have a premium design version that we will use when selling exclusive properties. Our company name is Harbourline Vale Estates and the name for this is exclusive selection is: 'The Harbourline Collection'. The design needs to work with our current brand, but have a distinctive PREMIUM feel to it. I have uploaded the barnd guidelines and also some of the exisisting logo variations. We do NOT need a new logo but feel free to play around with colours, fonts, sizes etc. for the sign.

Target Market(s)

Property buyers & house hunters

Industry/Entity Type

Real Estate - Residential Property

Font styles to use
Sans Serif

Requirements
Must have
• A premium fee, must be square design, must be easy to read when driving past the sign
Nice to have
• I'm open ot ideas

```html
<!DOCTYPE html>
<html lang="en">
<head>
<meta charset="utf-8">
<title>Harbourline Vale Estates – The Harbourline Collection For Sale Board</title>
<link rel="stylesheet" href="https://fonts.googleapis.com/css2?family=Inter:wght@200;300;600;800&display=swap">
<style>
  :root {
    --navy-deep: #0b0c4f;
    --navy-mid: #142a6e;
    --royal: #1f56a0;
    --glow: #2a6cb8;
    --white: #ffffff;
  }
  html, body {
    margin: 0;
    padding: 0;
    width: 1200px;
    height: 1200px;
    overflow: hidden;
    background: var(--navy-deep);
  }
  .sale-board {
    display: block;
    width: 1200px;
    height: 1200px;
    font-family: "Inter", "Helvetica Neue", Arial, sans-serif;
  }
  .brand-name { font-weight: 600; font-size: 31px; fill: var(--white); }
  .collection-title { font-weight: 200; font-size: 80px; fill: var(--white); letter-spacing: -1px; }
  .headline { font-weight: 800; font-size: 222px; fill: var(--white); }
  .phone { font-weight: 300; font-size: 160px; fill: var(--white); }
  .web-address { font-weight: 300; font-size: 38px; fill: var(--white); letter-spacing: -0.5px; }
  .divider, .rule { fill: var(--white); }
</style>
</head>
<body>
<svg class="sale-board" viewBox="0 0 1200 1200" xmlns="http://www.w3.org/2000/svg" aria-labelledby="board-title">
  <title id="board-title">Harbourline Vale Estates – The Harbourline Collection – For Sale</title>
  <defs>
    <linearGradient id="board-base" x1="0" y1="0" x2="0" y2="1">
      <stop offset="0" stop-color="#0b0c4f"/>
      <stop offset="0.35" stop-color="#0b0c4f"/>
      <stop offset="0.75" stop-color="#142a6e"/>
      <stop offset="1" stop-color="#1f56a0"/>
    </linearGradient>
    <radialGradient id="skyline-glow" cx="0.55" cy="1" r="0.75">
      <stop offset="0" stop-color="#2a6cb8" stop-opacity="0.95"/>
      <stop offset="0.55" stop-color="#1f56a0" stop-opacity="0.55"/>
      <stop offset="1" stop-color="#1f56a0" stop-opacity="0"/>
    </radialGradient>
  </defs>

  <rect class="board-background" width="1200" height="1200" fill="url(#board-base)"/>
  <rect class="skyline-illustration" role="img" aria-label="Faint illustration of a cathedral tower and town houses in soft blue tones" width="1200" height="1200" fill="url(#skyline-glow)"/>

  <g class="brand-block">
    <text class="brand-name" x="257" y="256" text-anchor="middle">Harbourline Vale Estates</text>
  </g>

  <rect class="divider" x="510" y="29" width="2" height="268"/>

  <g class="collection-block">
    <text class="collection-title" x="558" y="137">The Harbourline</text>
    <text class="collection-title" x="558" y="256">Collection</text>
  </g>

  <text class="headline" x="62" y="776" textLength="1076" lengthAdjust="spacingAndGlyphs">FOR SALE</text>
  <rect class="rule" x="62" y="816" width="1076" height="5"/>
  <text class="phone" x="62" y="966" textLength="1076" lengthAdjust="spacing">01632 960418</text>

  <text class="web-address" x="600" y="1148" text-anchor="middle">www.harbourlinevaleestates.co.uk</text>
</svg>
</body>
</html>
```